Private Investigation Business Card Design

I need a business card for a new private investigation company named Brisk Inquiries. I perform mainly surveillance jobs, vehicle repossessions, document serves etc. The final design should aim for a professional look. The logo has a magnifying glass with stick man arms and legs and is in a running action to show the "Brisk" aspect of the name. If the colour scheme could remain the same as the website www.briskinquiries-demo.com.au with silvers,blacks and a couple electric blue highlights.
Industry/Entity Type
Business
Contact Information for Business Card
Morgan Kellaway
Brisk Inquiries
0487316204
PO Box 58, Carnwell NSW 2291
info@briskinquiries-demo.com.au
www.briskinquiries-demo.com.au
Look and feel

```html
<!DOCTYPE html>
<html lang="en">
<head>
<meta charset="utf-8">
<title>Brisk Inquiries – Business Card</title>
<link href="https://fonts.googleapis.com/css2?family=Saira:wght@400;600;700&display=swap" rel="stylesheet">
<style>
  :root {
    --page: #ece9e4;
    --card-dark: #231f20;
    --card-light: #ffffff;
    --ink: #231f20;
    --silver: #b9b8bd;
    --silver-dark: #8c8b90;
    --web-grey: #bcbcbc;
  }
  * { margin: 0; padding: 0; box-sizing: border-box; }
  html, body {
    width: 1189px; height: 1200px; overflow: hidden;
    background: var(--page);
    font-family: "Saira", sans-serif;
  }
  .canvas { position: relative; width: 1189px; height: 1200px; }
  .card {
    position: absolute; left: 204px; width: 792px; height: 487px;
    box-shadow: 6px 8px 14px rgba(0,0,0,0.25);
  }
  .card--front { top: 68px; background: var(--card-dark); }
  .card--back { top: 627px; background: var(--card-light); }
  .brand {
    position: absolute; left: 90px; width: 612px;
    display: flex; align-items: center; gap: 34px;
  }
  .card--front .brand { top: 208px; }
  .card--back .brand { top: 80px; }
  .brand__name {
    font-weight: 600; font-size: 56px; letter-spacing: 1px;
    line-height: 1; white-space: nowrap;
  }
  .card--front .brand__name { color: var(--silver); }
  .card--back .brand__name { color: var(--silver-dark); }
  .brand__mark { width: 46px; height: 46px; border-radius: 50%; flex: none; }
  .card--front .brand__mark { background: var(--silver); }
  .card--back .brand__mark { background: var(--silver-dark); }
  .holder {
    position: absolute; top: 236px; left: 0; width: 100%;
    text-align: center; font-weight: 700; font-size: 36px;
    letter-spacing: 1.5px; color: var(--ink);
  }
  .contact {
    position: absolute; top: 312px; left: 0; width: 100%;
    text-align: center; font-size: 24px; line-height: 33px;
    color: var(--ink); letter-spacing: 0.8px;
  }
  .contact__label { font-weight: 700; }
  .web-band {
    position: absolute; left: 0; bottom: 0; width: 100%; height: 63px;
    background: var(--card-dark); color: var(--web-grey);
    font-size: 22px; letter-spacing: 1px;
    display: flex; align-items: center; justify-content: center;
  }
</style>
</head>
<body>
<div class="canvas">
  <section class="card card--front">
    <div class="brand">
      <span class="brand__name">Brisk Inquiries</span>
      <span class="brand__mark"></span>
    </div>
  </section>

  <section class="card card--back">
    <div class="brand">
      <span class="brand__name">Brisk Inquiries</span>
      <span class="brand__mark"></span>
    </div>
    <p class="holder">MORGAN KELLAWAY</p>
    <div class="contact">
      <p><span class="contact__label">P:</span> 0487316204</p>
      <p><span class="contact__label">E:</span> info@briskinquiries-demo.com.au</p>
      <p><span class="contact__label">A:</span> PO Box 58, Carnwell NSW 2291</p>
    </div>
    <div class="web-band">www.briskinquiries-demo.com.au</div>
  </section>
</div>
</body>
</html>
```